Business Card for a Dental Office

The design should communicate integrity, quality and reliability. We also want the card look elegant, simple, but still stand out, different from the traditional-dental-office business card.

Industry/Entity Type

Business

```html
<!DOCTYPE html>
<html lang="en">
<head>
<meta charset="utf-8">
<title>Harwick Dental Studio – Business Card</title>
<link rel="stylesheet" href="https://fonts.googleapis.com/css2?family=Bebas+Neue&family=Open+Sans:wght@400;600;700&display=swap">
<style>
  :root {
    --page-bg: #e9e7e3;
    --card-bg: #fbfbfa;
    --ink: #2f2f31;
    --ink-soft: #4a4a4d;
    --gold: #c9b22e;
    --rule: #3a3a3c;
  }
  * { box-sizing: border-box; margin: 0; padding: 0; }
  html, body {
    width: 1200px;
    height: 1022px;
    overflow: hidden;
    background: var(--page-bg);
  }
  body {
    display: flex;
    align-items: center;
    justify-content: center;
    font-family: "Open Sans", Arial, sans-serif;
  }
  .card {
    position: relative;
    width: 900px;
    height: 520px;
    background: var(--card-bg);
    box-shadow: 0 18px 40px rgba(0,0,0,0.18);
  }
  .divider {
    position: absolute;
    top: 0;
    bottom: 0;
    left: 732px;
    width: 2px;
    background: var(--rule);
  }
  .brand {
    position: absolute;
    left: 70px;
    top: 74px;
    display: flex;
    align-items: center;
    gap: 18px;
  }
  .brand-mark {
    width: 58px;
    height: 58px;
    background: var(--gold);
    flex: none;
  }
  .brand-name {
    font-family: "Bebas Neue", "Oswald", sans-serif;
    font-size: 50px;
    line-height: 0.9;
    color: var(--ink);
    letter-spacing: 0.5px;
  }
  .brand-tagline {
    font-family: "Bebas Neue", "Oswald", sans-serif;
    font-size: 22px;
    letter-spacing: 1.2px;
    color: var(--gold);
    margin-top: 2px;
  }
  .person {
    position: absolute;
    left: 70px;
    bottom: 60px;
    right: 168px;
  }
  .person-head {
    display: flex;
    align-items: flex-end;
    gap: 16px;
  }
  .person-name {
    font-weight: 700;
    font-size: 34px;
    letter-spacing: 1px;
    color: var(--ink-soft);
    line-height: 1;
    white-space: nowrap;
  }
  .person-rule {
    flex: 1;
    height: 2px;
    background: var(--rule);
    margin-bottom: 6px;
  }
  .person-role {
    font-size: 17px;
    letter-spacing: 2px;
    color: var(--gold);
    margin-top: 6px;
  }
  .contact-list {
    list-style: none;
    margin-top: 10px;
  }
  .contact-list li {
    display: flex;
    align-items: center;
    gap: 12px;
    font-size: 20px;
    color: var(--ink);
    line-height: 1.45;
    letter-spacing: 0.6px;
  }
  .contact-icon {
    width: 16px;
    height: 16px;
    flex: none;
  }
</style>
</head>
<body>
  <article class="card">
    <div class="divider"></div>

    <header class="brand">
      <span class="brand-mark"></span>
      <div>
        <div class="brand-name">Harwick Dental Studio</div>
        <div class="brand-tagline">Honest care for a lasting smile</div>
      </div>
    </header>

    <section class="person">
      <div class="person-head">
        <h1 class="person-name">MARA ELLISON</h1>
        <span class="person-rule"></span>
      </div>
      <p class="person-role">DIRECTOR</p>
      <ul class="contact-list">
        <li>
          <svg class="contact-icon" viewBox="0 0 16 16" aria-hidden="true">
            <path d="M3.5 1.5l2.5 3-1.6 1.6c.8 1.8 2.2 3.2 4 4l1.6-1.6 3 2.5-1.5 2.5C7 13 3 9 1 3z" fill="var(--gold)"/>
          </svg>
          +330 5172-0394
        </li>
        <li>
          <svg class="contact-icon" viewBox="0 0 16 16" aria-hidden="true">
            <rect x="1.5" y="3.5" width="13" height="9" fill="none" stroke="var(--gold)" stroke-width="1.6"/>
            <path d="M1.5 3.5L8 9l6.5-5.5" fill="none" stroke="var(--gold)" stroke-width="1.6"/>
          </svg>
          hello@harwickdental.com
        </li>
        <li>
          <svg class="contact-icon" viewBox="0 0 16 16" aria-hidden="true">
            <circle cx="8" cy="8" r="6.5" fill="none" stroke="var(--gold)" stroke-width="1.5"/>
            <ellipse cx="8" cy="8" rx="2.8" ry="6.5" fill="none" stroke="var(--gold)" stroke-width="1.2"/>
            <path d="M1.5 8h13" stroke="var(--gold)" stroke-width="1.2"/>
          </svg>
          www.harwickdental.com
        </li>
      </ul>
    </section>
  </article>
</body>
</html>
```